Quiet Harbor Podcast W/ Dr. Lena Marsh

Podcast Cover Art. I am in search of a re-design for my existing podcast. We have over 100 episodes, but I want to change the name to Quiet Harbor Podcast With Dr. Lena Marsh. I'm open to any ideas, and have attached source file image to use. ( note: NO brain images please).

```html
<!DOCTYPE html>
<html lang="en">
<head>
<meta charset="utf-8">
<title>Quiet Harbor Podcast with Dr. Lena Marsh</title>
<link rel="stylesheet" href="https://fonts.googleapis.com/css2?family=Poppins:wght@500;600;700&family=Great+Vibes&display=swap">
<style>
  :root {
    --page: #dadada;
    --paper: #ffffff;
    --paper-shade: #ececec;
    --coral: #fd6c51;
    --ink: #222222;
    --band: #232323;
    --white: #ffffff;
    --portrait-top: #e9c4a8;
    --portrait-bottom: #e4583a;
  }
  * { margin: 0; padding: 0; box-sizing: border-box; }
  html, body {
    width: 1106px;
    height: 1200px;
    overflow: hidden;
    background: var(--page);
  }
  .cover {
    position: absolute;
    left: 72px;
    top: 118px;
    width: 965px;
    height: 965px;
    overflow: hidden;
    background: linear-gradient(135deg, var(--paper) 0%, var(--paper-shade) 55%, var(--paper) 100%);
    font-family: "Poppins", sans-serif;
  }
  .host-portrait {
    position: absolute;
    left: 0;
    top: 0;
    width: 965px;
    height: 965px;
  }
  .title {
    position: absolute;
    left: 295px;
    top: 170px;
    width: 622px;
  }
  .title-main {
    display: block;
    font-weight: 700;
    font-size: 156px;
    line-height: 1;
    letter-spacing: -1px;
    color: var(--coral);
  }
  .title-sub {
    display: block;
    margin-top: -4px;
    font-weight: 600;
    font-size: 100px;
    line-height: 1.05;
    letter-spacing: -1px;
    color: var(--ink);
  }
  .title-rule {
    position: absolute;
    left: 295px;
    top: 423px;
    width: 617px;
    height: 4px;
    background: var(--coral);
  }
  .podcast-label {
    position: absolute;
    left: 395px;
    top: 458px;
    display: flex;
    align-items: center;
    gap: 20px;
  }
  .podcast-label .mic { width: 42px; height: 66px; }
  .podcast-label span {
    font-weight: 500;
    font-size: 50px;
    letter-spacing: 35px;
    margin-right: -35px;
    color: var(--ink);
    line-height: 1;
  }
  .host-band {
    position: absolute;
    left: 511px;
    top: 671px;
    width: 454px;
    height: 294px;
    background: var(--band);
    border-top: 7px solid var(--coral);
  }
  .host-with {
    position: absolute;
    left: 551px;
    top: 724px;
    font-family: "Great Vibes", cursive;
    font-size: 74px;
    line-height: 1;
    color: var(--coral);
  }
  .host-name {
    position: absolute;
    right: 53px;
    top: 792px;
    font-weight: 600;
    font-size: 47px;
    line-height: 1.2;
    color: var(--white);
    white-space: nowrap;
  }
</style>
</head>
<body>
  <main class="cover">
    <svg class="host-portrait" viewBox="0 0 965 965" role="img" aria-label="Illustrated portrait of the host, Dr. Lena Marsh">
      <defs>
        <linearGradient id="portraitTone" x1="0" y1="0" x2="0" y2="1">
          <stop offset="0" stop-color="var(--portrait-top)"/>
          <stop offset="0.5" stop-color="var(--portrait-top)"/>
          <stop offset="0.7" stop-color="var(--portrait-bottom)"/>
          <stop offset="1" stop-color="var(--portrait-bottom)"/>
        </linearGradient>
      </defs>
      <path fill="url(#portraitTone)" d="M0 200 H270 V610 H511 V965 H0 Z"/>
    </svg>

    <h1 class="title">
      <span class="title-main">QUIET</span>
      <span class="title-sub">HARBOR</span>
    </h1>
    <div class="title-rule"></div>

    <div class="podcast-label">
      <svg class="mic" viewBox="0 0 42 66" aria-hidden="true">
        <rect x="12" y="2" width="18" height="34" rx="9" fill="var(--coral)"/>
        <path d="M4 28 C4 40 12 46 21 46 C30 46 38 40 38 28" fill="none" stroke="var(--coral)" stroke-width="3"/>
        <line x1="21" y1="46" x2="21" y2="60" stroke="var(--coral)" stroke-width="3"/>
        <line x1="9" y1="61" x2="33" y2="61" stroke="var(--coral)" stroke-width="3"/>
        <g stroke="var(--white)" stroke-width="2">
          <line x1="12" y1="12" x2="19" y2="12"/>
          <line x1="12" y1="18" x2="19" y2="18"/>
          <line x1="12" y1="24" x2="19" y2="24"/>
        </g>
      </svg>
      <span>PODCAST</span>
    </div>

    <div class="host-band"></div>
    <p class="host-with">with</p>
    <p class="host-name">DR. LENA MARSH</p>
  </main>
</body>
</html>
```